Commercial Real Estate

We need a business card design for a new commercial real estate business that specializes in apartment building brokerage. Not individual units but the entire complex. We find and represent the owners existing buildings and well as new buyers for those buildings. The design should convey trust, integrity, knowledge and growth. It should be easily read.

Target Market(s)

40 to 65 years old

Industry/Entity Type

Real Estate

```html
<!DOCTYPE html>
<html lang="en">
<head>
<meta charset="utf-8">
<title>Alderway Property – Business Card</title>
<link rel="stylesheet" href="https://fonts.googleapis.com/css2?family=Open+Sans:ital,wght@0,300;0,400;0,600;1,600&display=swap">
<style>
  :root {
    --page-bg: #e9ebea;
    --card-bg: #ffffff;
    --slate: #5e6f6c;
    --teal: #5fc4b8;
    --ink: #3f4544;
    --ink-soft: #6b7371;
    --band-text: #ffffff;
  }
  * { box-sizing: border-box; margin: 0; padding: 0; }
  html, body {
    width: 1200px; height: 899px; overflow: hidden;
    background: var(--page-bg);
    font-family: "Open Sans", Arial, sans-serif;
  }
  .sheet {
    width: 1200px; height: 899px;
    display: flex; flex-direction: column;
    align-items: center; justify-content: center; gap: 44px;
  }
  .card {
    position: relative;
    width: 660px; height: 377px;
    background: var(--card-bg);
    border-radius: 34px;
    overflow: hidden;
    box-shadow: 0 6px 18px rgba(0,0,0,.12);
  }
  .card-art { position: absolute; inset: 0; }
  .identity {
    position: absolute; right: 40px; top: 54px;
    text-align: right; color: var(--band-text);
  }
  .identity-name { font-size: 25px; font-weight: 600; font-style: italic; letter-spacing: .2px; }
  .identity-role { font-size: 20px; font-weight: 300; margin-top: 2px; }
  .brand {
    position: absolute; display: flex; align-items: center; gap: 10px;
    color: var(--slate); font-weight: 600; letter-spacing: 1px;
    white-space: nowrap;
  }
  .brand-mark { background: var(--teal); flex: none; }
  .brand-name { display: flex; flex-direction: column; line-height: 1.15; }
  .card-front .brand { left: 46px; top: 222px; font-size: 20px; }
  .card-front .brand-mark { width: 16px; height: 16px; }
  .contact {
    position: absolute; left: 300px; top: 190px;
    padding-left: 20px; border-left: 1.5px solid var(--ink-soft);
    color: var(--ink); font-size: 17px; line-height: 1.42;
  }
  .contact-web { position: absolute; left: 300px; top: 330px; color: var(--ink); font-size: 17px; }
  .contact-line { display: flex; align-items: center; gap: 8px; }
  .contact-icon { width: 15px; height: 15px; fill: var(--ink); flex: none; }
  .card-back .brand {
    left: 50%; top: 50%; transform: translate(-50%, -50%);
    font-size: 34px;
  }
  .card-back .brand-name { flex-direction: row; gap: 0.3em; }
  .card-back .brand-mark { width: 24px; height: 24px; }
</style>
</head>
<body>
<main class="sheet">
  <section class="card card-front" aria-label="Business card front">
    <svg class="card-art" viewBox="0 0 660 377" aria-hidden="true">
      <path d="M0,0 H660 V215 C520,130 260,44 0,30 Z" fill="var(--slate)"/>
      <path d="M0,42 C260,56 520,140 660,226" fill="none" stroke="var(--teal)" stroke-width="5"/>
    </svg>
    <div class="identity">
      <p class="identity-name">Marlow Penhale</p>
      <p class="identity-role">Consultant</p>
    </div>
    <div class="brand"><span class="brand-mark"></span><span class="brand-name"><span>ALDERWAY</span><span>PROPERTY</span></span></div>
    <div class="contact">
      <p>41 Quarry Lane, 6th floor</p>
      <p>Easthaven</p>
      <p class="contact-line">
        <svg class="contact-icon" viewBox="0 0 16 16"><path d="M3 1h3l1.5 4-2 1.3a9 9 0 0 0 4.2 4.2L11 8.5l4 1.5v3a2 2 0 0 1-2 2A12 12 0 0 1 1 3a2 2 0 0 1 2-2z"/></svg>
        010 555 0142
      </p>
      <p class="contact-line">
        <svg class="contact-icon" viewBox="0 0 16 16"><path d="M4 1h7v4H4z M1 6h14v8H1z M4 9h8v2H4z"/></svg>
        010 555 0143
      </p>
      <p class="contact-line">
        <svg class="contact-icon" viewBox="0 0 16 16"><path d="M1 3h14v10H1z M2 4l6 5 6-5" stroke="#fff" stroke-width="1"/></svg>
        marlow@alderway.com
      </p>
    </div>
    <p class="contact-web">www.alderwayproperty.com</p>
  </section>

  <section class="card card-back" aria-label="Business card back">
    <div class="brand"><span class="brand-mark"></span><span class="brand-name"><span>ALDERWAY</span><span>PROPERTY</span></span></div>
  </section>
</main>
</body>
</html>
```